Bubble map/flip book

I need someone to create a bubble map with explanations using the attached. This will be used to create a color coded flip book/manual. I need you to clean this up.

Marlowesintary@quillpost.net

```html
<!DOCTYPE html>
<html lang="en">
<head>
<meta charset="utf-8">
<title>Denied Claims Flip Book – Page Overview</title>
<link rel="stylesheet" href="https://fonts.googleapis.com/css2?family=Open+Sans:wght@400;600;700;800&display=swap">
<style>
:root{
  --canvas:#8c8c8e;
  --yellow:#f5c400;
  --pink:#e8166a;
  --pink-deep:#d0103e;
  --green:#4b7f2c;
  --green-deep:#1f4a16;
  --brown:#8a5a12;
  --brown-deep:#5a300c;
  --purple:#4a2d8c;
  --purple-deep:#2c1a6e;
  --blue:#0b4f9c;
  --blue-deep:#0b2f6a;
  --orange:#f07a1a;
  --red:#e0331a;
  --ink:#222;
  --text:#333;
}
*{box-sizing:border-box;margin:0;padding:0}
html,body{width:1169px;height:1200px;overflow:hidden;background:var(--canvas);font-family:"Open Sans",sans-serif}
.sheet{position:relative;width:1169px;height:1200px}
.page{position:absolute;width:218px;height:282px;overflow:hidden;
  background:linear-gradient(155deg,#ffffff 0%,#f4f4f6 45%,#ebebee 100%)}
.wires{position:absolute;inset:0;width:218px;height:282px}
.box{position:absolute;display:flex;align-items:center;justify-content:center;text-align:center;
  color:#fff;font-size:4px;line-height:1.3;padding:2px;box-shadow:0 1px 2px rgba(0,0,0,.25);overflow:hidden}
.box.lg{font-size:5.4px}
.box.dark-text{color:var(--ink)}
.banner{position:absolute;left:14px;width:190px;display:flex;align-items:center;justify-content:center;
  text-align:center;color:#fff;font-weight:700;font-size:9px;line-height:1.15;box-shadow:0 2px 3px rgba(0,0,0,.3)}
.banner.dark-text{color:var(--ink)}
.title{position:absolute;left:20px;right:20px;text-align:center;font-weight:700;font-size:9.5px;line-height:1.15}
.rule{position:absolute;left:26px;right:26px;height:2.5px}
.body{position:absolute;left:24px;right:24px;font-size:3.6px;line-height:1.4;color:var(--text)}
.body p{margin-bottom:2px}
.body b{font-weight:700}
.body ul{list-style:none;margin-bottom:2px}
.corner{position:absolute;right:0;bottom:0;width:30px;height:30px}
.note{position:absolute;font-size:4px;line-height:1.4;color:var(--blue)}
</style>
</head>
<body>
<svg width="0" height="0" style="position:absolute">
  <defs>
    <marker id="a-yellow" viewBox="0 0 6 6" refX="5" refY="3" markerWidth="4" markerHeight="4" orient="auto"><path d="M0,0L6,3L0,6z" fill="#f5c400"/></marker>
    <marker id="a-pink" viewBox="0 0 6 6" refX="5" refY="3" markerWidth="4" markerHeight="4" orient="auto"><path d="M0,0L6,3L0,6z" fill="#e8166a"/></marker>
    <marker id="a-green" viewBox="0 0 6 6" refX="5" refY="3" markerWidth="4" markerHeight="4" orient="auto"><path d="M0,0L6,3L0,6z" fill="#4b7f2c"/></marker>
    <marker id="a-brown" viewBox="0 0 6 6" refX="5" refY="3" markerWidth="4" markerHeight="4" orient="auto"><path d="M0,0L6,3L0,6z" fill="#8a5a12"/></marker>
    <marker id="a-purple" viewBox="0 0 6 6" refX="5" refY="3" markerWidth="4" markerHeight="4" orient="auto"><path d="M0,0L6,3L0,6z" fill="#4a2d8c"/></marker>
    <marker id="a-blue" viewBox="0 0 6 6" refX="5" refY="3" markerWidth="4" markerHeight="4" orient="auto"><path d="M0,0L6,3L0,6z" fill="#0b4f9c"/></marker>
    <marker id="a-orange" viewBox="0 0 6 6" refX="5" refY="3" markerWidth="4" markerHeight="4" orient="auto"><path d="M0,0L6,3L0,6z" fill="#f07a1a"/></marker>
  </defs>
</svg>

<main class="sheet">

<!-- Row 1 -->
<section class="page" style="left:27px;top:26px">
  <svg class="wires" viewBox="0 0 218 282" fill="none" stroke-width=".8">
    <line x1="29" y1="72" x2="29" y2="148" stroke="var(--yellow)"/>
    <line x1="57" y1="72" x2="57" y2="188" stroke="var(--pink)"/>
    <line x1="82" y1="72" x2="82" y2="148" stroke="var(--green)"/>
    <line x1="110" y1="72" x2="110" y2="188" stroke="var(--brown)"/>
    <line x1="134" y1="72" x2="134" y2="148" stroke="var(--purple)"/>
    <line x1="162" y1="72" x2="162" y2="188" stroke="var(--blue)"/>
    <line x1="187" y1="72" x2="187" y2="148" stroke="var(--orange)"/>
  </svg>
  <div class="banner" style="left:17px;width:185px;top:42px;height:30px;background:var(--ink);font-size:10.5px">CLAIM HAS BEEN DENIED</div>
  <div class="box" style="left:9px;top:148px;width:40px;height:40px;background:var(--yellow)">Authorization Referral Needed</div>
  <div class="box" style="left:62px;top:148px;width:40px;height:40px;background:var(--green)">Duplicate</div>
  <div class="box" style="left:114px;top:148px;width:40px;height:40px;background:var(--purple)">Global Inclusive</div>
  <div class="box" style="left:167px;top:148px;width:40px;height:40px;background:var(--orange)">Post Timely Filing</div>
  <div class="box" style="left:37px;top:188px;width:41px;height:40px;background:var(--pink)">Coding/ Billing Issues</div>
  <div class="box" style="left:89px;top:188px;width:41px;height:40px;background:var(--brown)">Non-Covered Charge</div>
  <div class="box" style="left:142px;top:188px;width:41px;height:40px;background:var(--blue)">Additional Information Requested</div>
  <svg class="corner" viewBox="0 0 30 30"><polygon points="30,0 30,30 0,30" fill="var(--yellow)"/><polygon points="30,16 30,30 16,30" fill="#fbe27a"/></svg>
</section>

<section class="page" style="left:252px;top:26px">
  <svg class="wires" viewBox="0 0 218 282" fill="none" stroke="var(--yellow)" stroke-width=".8">
    <line x1="108" y1="70" x2="108" y2="82"/>
    <polyline points="108,108 108,114 53,114 53,128" marker-end="url(#a-yellow)"/>
    <polyline points="108,114 167,114 167,128" marker-end="url(#a-yellow)"/>
    <polyline points="53,172 53,180 26,180 26,196" marker-end="url(#a-yellow)"/>
    <polyline points="53,180 78,180 78,196" marker-end="url(#a-yellow)"/>
    <polyline points="167,172 167,180 151,180 151,196" marker-end="url(#a-yellow)"/>
    <polyline points="167,180 194,180 194,196" marker-end="url(#a-yellow)"/>
  </svg>
  <div class="banner dark-text" style="top:42px;height:28px;background:var(--yellow);font-size:8.4px">Claim denied for no authorization/referral.</div>
  <div class="box dark-text" style="left:58px;top:82px;width:100px;height:26px;background:var(--yellow)"><span><span style="font-size:5.4px">Contact carrier.</span><br><i>Was claim processed in network or out of network?</i></span></div>
  <div class="box" style="left:18px;top:128px;width:70px;height:44px;background:var(--yellow)">Claim processed correctly as in network provider. Medical records printed and sent for medical necessity.</div>
  <div class="box" style="left:132px;top:128px;width:70px;height:44px;background:var(--yellow)">Claim processed out of network. Contact with carrier shows claim processed as out of network in error. Will rep send claim back?</div>
  <div class="box" style="left:10px;top:196px;width:32px;height:48px;background:var(--yellow)">Appeal denied as services were not emergent. Balance is patient responsibility.</div>
  <div class="box" style="left:62px;top:196px;width:32px;height:48px;background:var(--yellow)">Appeal for claim paid.</div>
  <div class="box" style="left:135px;top:196px;width:32px;height:48px;background:var(--yellow)">Claim has been sent back for review. Follow up in 14 days.</div>
  <div class="box" style="left:178px;top:196px;width:32px;height:48px;background:var(--yellow)">Rep will not send claim back. Appeal sent to carrier. Follow up in 30 days.</div>
  <svg class="corner" viewBox="0 0 30 30"><polygon points="30,0 30,30 0,30" fill="var(--yellow)"/><polygon points="30,16 30,30 16,30" fill="#fbe27a"/></svg>
</section>

<section class="page" style="left:477px;top:26px">
  <div class="title" style="top:20px;color:var(--yellow)">Authorization/referral needed.</div>
  <div class="rule" style="top:35px;background:var(--yellow)"></div>
  <div class="body" style="top:58px">
    <p>1. If you are a network provider verify that the claim processed correctly in network. If claim processed out of network have the claim sent back to process or send appeal stating that claim processed incorrectly out of network.</p>
    <p>2. If you are not a network provider you may send an appeal with medical records attached stating to reprocess and pay claim based on medical necessity.</p>
    <p><b>NOTES ON ACCOUNT SHOULD INCLUDE:</b></p>
    <ul><li>- Claim number</li><li>- Denial date</li><li>- Processed in or out of network</li></ul>
  </div>
  <svg class="corner" viewBox="0 0 30 30"><polygon points="30,0 30,30 0,30" fill="var(--yellow)"/><polygon points="30,16 30,30 16,30" fill="#fbe27a"/></svg>
</section>

<section class="page" style="left:702px;top:26px">
  <svg class="wires" viewBox="0 0 218 282" fill="none" stroke="var(--pink)" stroke-width=".8">
    <line x1="108" y1="68" x2="108" y2="80"/>
    <polyline points="108,102 108,110 50,110 50,128" marker-end="url(#a-pink)"/>
    <polyline points="108,110 168,110 168,128" marker-end="url(#a-pink)"/>
    <polyline points="168,170 168,180 148,180 148,196" marker-end="url(#a-pink)"/>
    <polyline points="168,180 188,180 188,196" marker-end="url(#a-pink)"/>
  </svg>
  <div class="banner" style="top:38px;height:30px;background:var(--pink)">Coding Denial<br>CPT/DX/Modifier</div>
  <div class="box lg" style="left:58px;top:80px;width:100px;height:22px;background:var(--pink)">Contact made with carrier.</div>
  <div class="box" style="left:18px;top:128px;width:64px;height:42px;background:var(--pink)">Claim denied in error and has been sent back to process.</div>
  <div class="box" style="left:134px;top:128px;width:68px;height:42px;background:var(--pink-deep)">Claim denied correctly for coding error</div>
  <div class="box" style="left:134px;top:196px;width:28px;height:44px;background:var(--pink-deep)">Forwarded to physician for review</div>
  <div class="box" style="left:174px;top:196px;width:28px;height:44px;background:var(--pink-deep)">Corrected and rebilled as a corrected claim</div>
  <svg class="corner" viewBox="0 0 30 30"><polygon points="30,0 30,30 0,30" fill="var(--pink)"/><polygon points="30,16 30,30 16,30" fill="#f37aa6"/></svg>
</section>

<section class="page" style="left:927px;top:26px">
  <div class="title" style="top:20px;color:var(--pink)">Coding Denial</div>
  <div class="rule" style="top:35px;background:var(--pink)"></div>
  <div class="body" style="top:50px">
    <p><b>Example:</b><br>*Claim denied as procedure code used 99203 is for a new patient and this is an established patient.</p>
    <p><b>ACCOUNT NOTE WILL INCLUDE:</b></p>
    <ul><li>* How information was obtained</li><li>* Name a representative</li><li>* Claim number</li><li>* Denial date</li><li>* What was denied: CPT, HCPCS, modifier, diagnosis?</li><li>* What code denied?</li><li>* Why was it denied?</li><li>A. Not covered?</li><li>B. Bundled to another code on the claim? Which code is it bundled with?</li><li>C. Not a covered benefit per patient policy? What is the service?</li><li>D. Invalid modifier? What modifier was billed? What is needed?</li><li>G. Diagnosis does not match CPT? Verify codes billed do not relate to each other.</li><li>*Appeal address</li><li>*Timely filing</li></ul>
    <p style="margin-top:3px"><b>*Verify that the claim was billed with the CPT code stated.</b></p>
  </div>
  <svg class="corner" viewBox="0 0 30 30"><polygon points="30,0 30,30 0,30" fill="var(--pink)"/><polygon points="30,16 30,30 16,30" fill="#f37aa6"/></svg>
</section>

<!-- Row 2 -->
<section class="page" style="left:27px;top:315px">
  <svg class="wires" viewBox="0 0 218 282" fill="none" stroke="var(--green)" stroke-width=".8">
    <line x1="109" y1="64" x2="109" y2="76"/>
    <polyline points="109,98 109,106 51,106 51,124" marker-end="url(#a-green)"/>
    <polyline points="109,106 167,106 167,124" marker-end="url(#a-green)"/>
    <polyline points="51,174 51,182 26,182 26,194" marker-end="url(#a-green)"/>
    <polyline points="51,182 78,182 78,194" marker-end="url(#a-green)"/>
  </svg>
  <div class="banner" style="top:38px;height:26px;background:var(--green)">Claim denied as a duplicate</div>
  <div class="box lg" style="left:48px;top:76px;width:122px;height:22px;background:var(--green)">Verify that your office has not sent two claims for this date of service</div>
  <div class="box" style="left:14px;top:124px;width:74px;height:50px;background:var(--green)">Only 1 claim billed. Contact with carrier shows other claim billed under a different NPI or Tax ID. Will rep send claim back to process?</div>
  <div class="box" style="left:130px;top:124px;width:74px;height:50px;background:var(--green-deep)">Two claims billed. If additional charges were added combine charges and rebill as corrected claim. If two identical claims sent in error void claim.</div>
  <div class="box" style="left:12px;top:194px;width:28px;height:48px;background:var(--green)">Rep sent claim back to process for payment</div>
  <div class="box" style="left:64px;top:194px;width:28px;height:56px;background:var(--green)">Rep will not send claim back to process. Send appeal with medical records</div>
  <svg class="corner" viewBox="0 0 30 30"><polygon points="30,0 30,30 0,30" fill="var(--green)"/><polygon points="30,16 30,30 16,30" fill="#8fbf6a"/></svg>
</section>

<section class="page" style="left:252px;top:315px">
  <div class="title" style="top:20px;color:var(--green)">Duplicate</div>
  <div class="rule" style="top:35px;background:var(--green)"></div>
  <div class="body" style="top:46px;font-size:3.3px">
    <p>Review the record to verify that the service rendered was actually performed and billed just once. If the service has been performed and billed only once, then contacting the insurance company and reviewing the claim with a claims specialist may be the best option.</p>
    <p>Duplicate service denial is indicated when the same service was performed on the same patient on the same date by the same provider.</p>
    <p><b>Three reasons a claim may be denied as duplicate:</b><br>1. The service was performed more than once on the same day.<br>2. The service was performed once but billed twice.<br>3. Another physician performed the same service on the same date and submitted a claim with the same CPT code you did.</p>
    <p><b>How to respond to a claim denied as a duplicate:</b><br>1. If the service was performed more than once on the same day it may be eligible for a modifier. Modifier 59, RT and LT may be appended to indicate the procedure was performed bilaterally or at a separate session. If a modifier is needed, correct the claim and resubmit it as a corrected claim with a copy of the report.</p>
    <p>2. If you find you have actually submitted the claim twice then you may need to verify a few things:</p>
    <ul><li>• Was payment made on the first claim and if yes, was it sent to the correct address?</li><li>• Has the check been deposited and somehow missed in the posting process?</li><li>• Was the payment sent to the patient for failure to check the accept assignment box?</li><li>• Was the first claim submitted denied? If denied, was the denial handled correctly?</li></ul>
    <p>3. If another provider has performed the same service and was paid while your claim was denied you may need to speak to your insurance representative to determine the proper method of appeal. In short, a denial for duplicate service does not mean the claim will never be paid.</p>
  </div>
  <svg class="corner" viewBox="0 0 30 30"><polygon points="30,0 30,30 0,30" fill="var(--green)"/><polygon points="30,16 30,30 16,30" fill="#8fbf6a"/></svg>
</section>

<section class="page" style="left:477px;top:315px">
  <svg class="wires" viewBox="0 0 218 282" fill="none" stroke="var(--brown)" stroke-width=".8">
    <line x1="108" y1="64" x2="108" y2="80"/>
    <polyline points="108,106 108,114 53,114 53,128" marker-end="url(#a-brown)"/>
    <polyline points="108,114 167,114 167,128" marker-end="url(#a-brown)"/>
    <polyline points="53,190 53,198 28,198 28,208" marker-end="url(#a-brown)"/>
    <polyline points="53,198 78,198 78,208" marker-end="url(#a-brown)"/>
  </svg>
  <div class="banner" style="top:38px;height:26px;background:var(--brown)">Claim denied as Non-covered</div>
  <div class="box lg" style="left:48px;top:80px;width:120px;height:26px;background:var(--brown)">Contact Carrier.</div>
  <div class="box" style="left:14px;top:128px;width:78px;height:62px;background:var(--brown)"><span>Claim denied correctly. What is non-covered: <i>The diagnosis or CPT Code?</i><br><br><i>Is the diagnosis a policy exclusion? Send back to the physician to see if diagnosis can be changed</i></span></div>
  <div class="box" style="left:132px;top:128px;width:70px;height:40px;background:var(--brown-deep)">Claim denied in error and claim has been sent back to process</div>
  <div class="box" style="left:14px;top:208px;width:28px;height:40px;background:var(--brown)">Dx updated and claim rebilled as corrected claim</div>
  <div class="box" style="left:64px;top:208px;width:28px;height:56px;background:var(--brown)">Physician unable to change Dx. Appeal with medical records</div>
  <svg class="corner" viewBox="0 0 30 30"><polygon points="30,0 30,30 0,30" fill="var(--brown)"/><polygon points="30,16 30,30 16,30" fill="#c29a52"/></svg>
</section>

<section class="page" style="left:702px;top:315px">
  <div class="title" style="top:20px;color:var(--brown)">Non-covered</div>
  <div class="rule" style="top:35px;background:var(--brown)"></div>
  <div class="body" style="top:46px">
    <p>Insurance companies determine what tests, drugs and services they will cover. These choices are based on their understanding of the kinds of medical care that most patients need. The insurance company's choices may mean that the test, drug, or service you provided isn't covered by the policy.</p>
    <ul><li>• It is better to know what the insurance company will pay for before you provide a service, test or fill a prescription. Some kinds of care may have to be approved by the insurance company before you can provide them.</li></ul>
    <p>When a test or treatment isn't covered the insurance company won't pay the bill. This is called "denying the claim." If your insurance company denies your claim, you have the right to appeal the decision.</p>
  </div>
  <svg class="corner" viewBox="0 0 30 30"><polygon points="30,0 30,30 0,30" fill="var(--brown)"/><polygon points="30,16 30,30 16,30" fill="#c29a52"/></svg>
</section>

<section class="page" style="left:927px;top:315px">
  <svg class="wires" viewBox="0 0 218 282" fill="none" stroke="var(--purple)" stroke-width=".8">
    <line x1="109" y1="64" x2="109" y2="114"/>
    <polyline points="109,114 43,114 43,136" marker-end="url(#a-purple)"/>
    <polyline points="109,114 169,114 169,136" marker-end="url(#a-purple)"/>
  </svg>
  <div class="banner" style="top:38px;height:26px;background:var(--purple)">Claim denied as Global Inclusive</div>
  <div class="box" style="left:18px;top:136px;width:50px;height:40px;background:var(--purple)">Claim denied and has been sent back to process</div>
  <div class="box" style="left:134px;top:136px;width:70px;height:40px;background:var(--purple-deep)">Claim is global inclusive to claim resolved accounts</div>
  <svg class="corner" viewBox="0 0 30 30"><polygon points="30,0 30,30 0,30" fill="var(--purple)"/><polygon points="30,16 30,30 16,30" fill="#8f78c9"/></svg>
</section>

<!-- Row 3 -->
<section class="page" style="left:27px;top:604px">
  <div class="title" style="top:20px;color:var(--purple)">GLOBAL SURGICAL PACKAGE</div>
  <div class="rule" style="top:35px;background:var(--purple)"></div>
  <div class="body" style="top:52px">
    <ul><li>• The global surgical package is a single payment for all care associated with a surgical procedure. Within 10 days.</li><li>• Other names for the Global Surgical Package include: Postoperative Period, Global Period, Global Services, Surgical Period, Global package and Global Surgery.</li><li>• Care of a patient during the global surgical period is not restricted to any specific location. A patient may be treated by the surgeon in any setting including inpatient hospital, outpatient hospital, ambulatory surgical center, nursing home, surgeon's office, emergency room, urgent care, and even the intensive care unit of a hospital.</li></ul>
  </div>
  <div class="title" style="top:142px;color:var(--purple)">NO CHARGE SERVICES</div>
  <div class="rule" style="top:157px;background:var(--purple)"></div>
  <div class="body" style="top:170px">
    <p>There are several services that are not charged services as they are associated with another service.</p>
    <ul><li>• Suture removal placed at this office</li><li>• Routine I&amp;D follow up</li><li>• Sprain follow up</li><li>• Corneal abrasion follow up</li></ul>
  </div>
  <svg class="corner" viewBox="0 0 30 30"><polygon points="30,0 30,30 0,30" fill="var(--purple)"/><polygon points="30,16 30,30 16,30" fill="#8f78c9"/></svg>
</section>

<section class="page" style="left:252px;top:604px">
  <svg class="wires" viewBox="0 0 218 282" fill="none" stroke="var(--blue)" stroke-width=".8">
    <line x1="109" y1="64" x2="109" y2="104"/>
    <polyline points="109,104 67,104 67,122" marker-end="url(#a-blue)"/>
    <polyline points="109,104 151,104 151,122" marker-end="url(#a-blue)"/>
    <polyline points="67,166 67,180 94,180" marker-end="url(#a-blue)"/>
    <polyline points="151,166 151,180 126,180" marker-end="url(#a-blue)"/>
    <polyline points="58,166 58,216 94,216" marker-end="url(#a-blue)"/>
    <polyline points="160,166 160,216 126,216" marker-end="url(#a-blue)"/>
    <line x1="110" y1="194" x2="110" y2="205" marker-end="url(#a-blue)"/>
  </svg>
  <div class="banner" style="top:34px;height:30px;background:var(--blue)">Additional Information Requested</div>
  <div class="note" style="left:22px;top:128px;width:26px">* Primary EOB<br><br>* Medical Records</div>
  <div class="box" style="left:48px;top:122px;width:38px;height:44px;background:var(--blue)"><span>Additional information requested from provider.<br><i>See Attachment</i></span></div>
  <div class="box" style="left:132px;top:122px;width:38px;height:44px;background:var(--blue-deep)"><span>Additional information requested from patient.<br><i>See Attachment</i></span></div>
  <div class="note" style="left:172px;top:128px;width:36px">* COB Update<br><br>* Third party liability form</div>
  <div class="box" style="left:94px;top:172px;width:32px;height:22px;background:var(--blue)">Applied to patient responsibility</div>
  <div class="box" style="left:94px;top:206px;width:32px;height:20px;background:var(--blue)">Claim paid</div>
  <svg class="corner" viewBox="0 0 30 30"><polygon points="30,0 30,30 0,30" fill="var(--blue)"/><polygon points="30,16 30,30 16,30" fill="#6f9bd2"/></svg>
</section>

<section class="page" style="left:477px;top:604px">
  <div class="title" style="top:14px;color:var(--blue);font-size:8.6px">Claim has been denied requesting additional information from the patient:</div>
  <div class="rule" style="top:38px;background:var(--blue)"></div>
  <div class="body" style="top:50px">
    <p style="color:var(--blue)"><b>Carrier Questions for note:</b></p>
    <ul><li>* Who did you speak to?</li><li>* What is the phone number?</li><li>* What is the claim number?</li><li>* When did the claim deny?</li><li>* What has been requested from the patient? When was the patient last contacted?</li><li>* How can the patient respond to your request? Fax? Phone? Mail?</li></ul>
    <p>* Claim denied for Third Party Liability Form/Accident Details (TPL): verify via the practice system that the service performed was due to an injury by going to the history tab and double clicking on the date of service. Below was Acute frontal sinusitis, unspecified. Obviously not an injury. If services was not for an injury have the rep send claim back to process.</p>
    <p>* Claim denied for Coordination of Benefits update (COB). Ask what other carrier they are showing on file. ID number etc.</p>
    <p>* Claim denied for missing or incomplete policy information. What is missing? Have other claims paid? How?</p>
    <p>* Make sure it is in Display mode and hit Save. This will create a pop up note every time someone goes into the account.</p>
    <p>* Add your note to the account. Account note should end with "printed letter to send to the patient.</p>
    <p>* Set next action code to: Pending information from patient. Set follow up for 2 weeks.</p>
    <p>* Follow up on the account in 2 weeks. If patient has not responded move balance to patient responsibility, deductible and note the account.</p>
  </div>
  <svg class="corner" viewBox="0 0 30 30"><polygon points="30,0 30,30 0,30" fill="var(--blue)"/><polygon points="30,16 30,30 16,30" fill="#6f9bd2"/></svg>
</section>

<section class="page" style="left:702px;top:604px">
  <div class="title" style="top:22px;color:var(--blue);font-size:8.4px">Pending Information from the Patient</div>
  <div class="rule" style="top:34px;background:var(--blue)"></div>
  <div class="body" style="top:42px;left:16px;right:16px;font-size:3px">
    <p>1) Claim has been denied or pended by the carrier requesting additional information from the patient:</p>
    <p>What is included in account note:<br>* How information was obtained.<br>* Phone number<br>* Claim number<br>* Denial date<br>* What has been requested from the patient<br>* When was the patient last contacted<br>* How can the patient respond to request (phone, mail, fax)<br>* Timely filing limit</p>
    <p>2) Third Party Liability Form/Accident Details (TPL)<br>a. Verify via the practice system that the service performed was due to an injury by going to the history tab and double clicking on the date of service of the claim.<br>b. Click on the diagnosis code and it will show why patient was seen. If services was not for an injury have the rep send claim back to process.<br>c. If claim was accurately denied for TPL, in the patient chart, under forms, select the TPL letter.<br>d. Print the populated form letter to the printer.<br>e. Notate the account that the first TPL letter has been printed.<br>f. Add a note to the account once the first letter is sent.<br>g. You will also need to add a Memo tab in the patient chart indicating text: "This patient's accounts are currently pended by their insurance for third party liability details. Please have patient contact their insurance to update."<br>h. Set the next action code to pending information from patient. Set follow up for 2 weeks.<br>i. If in two weeks there has been no response to the TPL letter directly by the patient, print a second TPL letter and follow up for 3 weeks.<br>j. If TPL details have been updated by the carrier please have the claim reprocessed and notate accordingly.<br>k. If TPL details have NOT been updated please write off the balance to bad debt and notate the account accordingly.</p>
  </div>
  <svg class="corner" viewBox="0 0 30 30"><polygon points="30,0 30,30 0,30" fill="var(--blue)"/><polygon points="30,16 30,30 16,30" fill="#6f9bd2"/></svg>
</section>

<section class="page" style="left:927px;top:604px">
  <div class="title" style="top:22px;color:var(--blue);font-size:8.4px">Pending Information from the Patient</div>
  <div class="rule" style="top:34px;background:var(--blue)"></div>
  <div class="body" style="top:42px;left:16px;right:16px;font-size:3px">
    <p>3) Coordination of Benefits (COB) details<br>a. Request for the carrier to validate those details have not been updated already.<br>i. If they have not, please proceed to submit the COB letter to the patient.<br>1. If claim was accurately denied for COB, in the patient chart, under forms, select the COB letter.<br>2. Print the populated form letter to the printer.<br>3. Notate the account that the first COB letter has been printed.<br>4. Add a note to the account once the first letter is sent.<br>5. You will also need to add a Memo tab in the patient chart indicating text: "This patient's accounts are currently pended by their insurance for coordination of benefit details. Please have patient contact their insurance to update."<br>6. Set the next action code to pending information from patient. Set follow up for 2 weeks.<br>7. If in two weeks there has been no response, print a second COB letter and follow up for 3 weeks.<br>8. If COB details have been updated by the carrier please have the claim reprocessed and notate accordingly.<br>9. If COB details have NOT been updated please write off the balance to bad debt.<br>10. If they have, please request the claim be reprocessed.</p>
    <p>4) Coverage was not in effect for the date of service<br>a. If the carrier states there was no coverage for the date of service<br>i. Please identify the date that coverage terminated<br>ii. If the patient never showed as having coverage, confirm you have the right patient details by referencing the chart scanned documents.<br>iii. Populate and print the coverage letter to the printer and notate the account.<br>1. Add a memo to the notes tab that the patient coverage was not in effect for the date of service and to please obtain updated insurance details.<br>2. Update the action step to pending information from the patient and set the tickler to 3 weeks.<br>iv. If there is no response from the patient at three weeks the balance should be written off as bad debt.<br>v. If the patient responds to the letter then the new insurance should be billed.</p>
  </div>
  <svg class="corner" viewBox="0 0 30 30"><polygon points="30,0 30,30 0,30" fill="var(--blue)"/><polygon points="30,16 30,30 16,30" fill="#6f9bd2"/></svg>
</section>

<!-- Row 4 -->
<section class="page" style="left:27px;top:893px">
  <div class="title" style="top:22px;color:var(--blue);font-size:8.4px">Pending information from provider</div>
  <div class="rule" style="top:34px;background:var(--blue)"></div>
  <div class="body" style="top:44px;left:20px;right:20px">
    <p style="color:var(--blue);font-size:5.2px;font-weight:700;margin-bottom:4px">Primary EOB required</p>
    <p><b>Account note will include:</b><br>*How information was obtained<br>*Name of representative<br>*Phone number<br>*Claim number<br>* Denial date<br>*Name of primary carrier on file</p>
    <p>1. Claim has previously been billed to the primary carrier: Print EOB and rebill with claim.</p>
    <p>2. Claim was not sent to primary carrier: Send claim to that carrier.</p>
    <p>3. Claim was not billed to primary carrier as the patient did not inform clinic of other insurance coverage. Representative supplies primary carrier on file. Call will be made to the carrier to verify ID number, group number, effective dates, claim address, timely filing deadline. Insurance information will be added to patient information and claim will be sent.</p>
    <p>4. Claim was not billed to the primary carrier, representative did not give other health insurance information. Patient will be sent Coordination of Benefits letter.</p>
  </div>
  <svg class="corner" viewBox="0 0 30 30"><polygon points="30,0 30,30 0,30" fill="var(--blue)"/><polygon points="30,16 30,30 16,30" fill="#6f9bd2"/></svg>
</section>

<section class="page" style="left:252px;top:893px">
  <svg class="wires" viewBox="0 0 218 282" fill="none" stroke="var(--orange)" stroke-width=".8">
    <line x1="109" y1="64" x2="109" y2="158" marker-end="url(#a-orange)"/>
    <polyline points="109,90 50,90 50,106" marker-end="url(#a-orange)"/>
    <polyline points="109,90 166,90 166,106" marker-end="url(#a-orange)"/>
    <line x1="109" y1="214" x2="109" y2="242" marker-end="url(#a-orange)"/>
  </svg>
  <div class="banner" style="top:34px;height:30px;background:var(--orange);font-size:8.6px">Claim/appeal denied for past timely filing.</div>
  <div class="box" style="left:30px;top:106px;width:40px;height:48px;background:var(--orange)">Claim is not past timely filing and rep. sends claim back to process.</div>
  <div class="box" style="left:146px;top:106px;width:40px;height:48px;background:var(--red)">Account is past filing deadline.</div>
  <div class="box" style="left:88px;top:158px;width:42px;height:56px;background:var(--red)">Rep. will not send claim back to process, but you find proof that claim was not past filing deadline.</div>
  <div class="box" style="left:88px;top:242px;width:42px;height:18px;background:var(--red)">Timely filing appeal sent.</div>
  <svg class="corner" viewBox="0 0 30 30"><polygon points="30,0 30,30 0,30" fill="var(--orange)"/><polygon points="30,16 30,30 16,30" fill="#f7b072"/></svg>
</section>

<section class="page" style="left:477px;top:893px">
  <div class="title" style="top:20px;color:var(--orange)">Past Timely Filing</div>
  <div class="rule" style="top:35px;background:var(--orange)"></div>
  <div class="body" style="top:52px;left:30px">
    <p>* Carrier filing limits:</p>
    <ul style="padding-left:8px"><li>Harborline: Claims 60 days appeals: 180 days</li><li>Stonegate: Claim: 120 days appeals: 180 days</li><li>Brightwell: Claim: 90 days</li><li>Kestrel: Claim: 90 days appeals: 180 days</li><li>Fernway: Claim: 180 days</li><li>Oakridge: Claim: 90 days appeals: 18 months</li><li>Northpoint: 365 days</li><li>Silverbay: Claim: 90 days</li><li>Redmont: 365 days</li></ul>
    <p style="margin-top:3px">Account notes will include:</p>
    <ul style="padding-left:8px"><li>* Claim number</li><li>* Denial date</li><li>* Date the claim/appeal was received.</li><li>* Filing deadline</li><li>* Date original (first) claim or appeal was received?</li><li>* Appeal address</li><li>* Appeal timely filing</li></ul>
    <ul style="padding-left:8px;margin-top:3px"><li>* Claim is not past timely filing have the representative send the claim back to process.</li><li>* If rep. will not send claim back to process. Send appeal.</li></ul>
  </div>
  <svg class="corner" viewBox="0 0 30 30"><polygon points="30,0 30,30 0,30" fill="var(--orange)"/><polygon points="30,16 30,30 16,30" fill="#f7b072"/></svg>
</section>

</main>
</body>
</html>
```